Classy, Elegant, Simple Business Card Design

Looking to have a classy, simple, and elegant design. Want a top notch designed business card. I really like the look of the new torvane credit card. I also like the design I attached. I am trying to reach 21-29 year old females for booking us for there wedding or event. We offer Disc Jockey Service, Photo Booth Rentals, and Uplighting .

Target Market(s)

21-28 year old females

Contact Information for Business Card

Has to have logo, website, email, and phone number

Font styles to use
Other font styles liked:
• open to font choice, modern, clean
Designer to choose
33a6d7
0791cd
0555a3
ffffff

Requirements
Must have
• Has to have logo, website, email, and phone number
Nice to have
• I really like the design of the new torvane credit card. I also included my logo and some designs I like
Should not have
• clutter or too much info

```html
<!DOCTYPE html>
<html lang="en">
<head>
<meta charset="utf-8">
<title>Lumentide Event Group – Business Card</title>
<link href="https://fonts.googleapis.com/css2?family=Lato:wght@400;700&family=Josefin+Sans:wght@300;400&display=swap" rel="stylesheet">
<style>
  :root {
    --stage: #d9d9d9;
    --navy: #155b97;
    --sky: #0a9ae0;
    --brand-blue: #0555a3;
    --ink-white: #ffffff;
    --card-white: #f8f8f8;
    --muted: #8a8a8a;
  }
  * { box-sizing: border-box; margin: 0; padding: 0; }
  html, body { width: 1200px; height: 802px; overflow: hidden; }
  body { background: var(--stage); position: relative; font-family: "Lato", sans-serif; }

  .card {
    position: absolute;
    top: 274px;
    width: 442px;
    height: 264px;
    overflow: hidden;
  }
  .card--back { left: 136px; background: var(--navy); color: var(--ink-white); }
  .card--front { left: 624px; background: var(--card-white); }

  .card__decor { position: absolute; inset: 0; }

  .contact-list, .service-list { position: absolute; left: 20px; list-style: none; }
  .contact-list { top: 61px; }
  .contact-list li {
    display: flex; align-items: center; gap: 4px;
    font-size: 15px; line-height: 20px; height: 20px;
  }
  .contact-list svg { width: 16px; height: 16px; flex: none; }
  .service-list { top: 145px; }
  .service-list li {
    display: flex; align-items: center; gap: 6px;
    font-size: 15px; line-height: 20px;
  }
  .service-list li::before {
    content: ""; width: 7px; height: 7px; border-radius: 50%;
    background: var(--ink-white); flex: none;
  }

  .brand {
    position: absolute; left: 0; right: 0; top: 72px;
    display: flex; flex-direction: column; align-items: center;
  }
  .brand__dot { width: 62px; height: 62px; border-radius: 50%; background: var(--sky); margin-bottom: 12px; }
  .brand__name {
    font-family: "Josefin Sans", sans-serif; font-weight: 400;
    font-size: 27px; letter-spacing: 0.5px; color: var(--brand-blue); line-height: 1;
  }
  .brand__tag {
    font-family: "Josefin Sans", sans-serif; font-weight: 300;
    font-size: 11px; letter-spacing: 7px; color: var(--muted); margin-top: 6px; padding-left: 7px;
  }
</style>
</head>
<body>
  <section class="card card--back">
    <svg class="card__decor" viewBox="0 0 442 264" role="img" aria-label="Large brand monogram decoration in white and sky blue">
      <circle cx="330" cy="200" r="118" fill="var(--sky)"/>
    </svg>

    <ul class="contact-list">
      <li>
        <svg viewBox="0 0 16 16" aria-hidden="true"><circle cx="8" cy="8" r="8" fill="#fff"/><path d="M4.5 6.5c0-1 1-1.8 3.5-1.8s3.5.8 3.5 1.8l-1.4.4-.4-1H6.3l-.4 1zM5.5 8h5l.8 3.2H4.7z" fill="var(--navy)"/></svg>
        044-318 672 540
      </li>
      <li>
        <svg viewBox="0 0 16 16" aria-hidden="true"><circle cx="8" cy="8" r="8" fill="#fff"/><rect x="4" y="5" width="8" height="6" fill="none" stroke="var(--navy)" stroke-width="1.2"/><path d="M4 5l4 3.5L12 5" fill="none" stroke="var(--navy)" stroke-width="1.2"/></svg>
        hello@lumentide.com
      </li>
      <li>
        <svg viewBox="0 0 16 16" aria-hidden="true"><circle cx="8" cy="8" r="8" fill="#fff"/><path d="M8 3.5a3 3 0 0 0-3 3c0 2.3 3 6 3 6s3-3.7 3-6a3 3 0 0 0-3-3z" fill="var(--navy)"/><circle cx="8" cy="6.5" r="1.1" fill="#fff"/></svg>
        www.lumentide.com
      </li>
    </ul>

    <ul class="service-list">
      <li>Disc Jockey Service</li>
      <li>Photo Booth Rentals</li>
      <li>Uplighting</li>
    </ul>
  </section>

  <section class="card card--front">
    <div class="brand">
      <span class="brand__dot" aria-hidden="true"></span>
      <span class="brand__name">LUMENTIDE</span>
      <span class="brand__tag">EVENT GROUP</span>
    </div>
  </section>
</body>
</html>
```